Business Cards Needed for Innovative Healthcare Marketing Company

We are a marketing company focused on healthcare. Our company is all about rebranding yourself renewing your image and generating results. The phoenix stands for "reborn" or "rising" which we provide new brands for our clients we take their old brands and renew it with creativity and innovation. I am looking for a business card with color dimension. I have attached an example of a card I think has the look and feel of what I am trying to accomplish. I like that the card example has black and grey font colors, I like the font placement and the small logo, I really like the use of the colors on the right those are the colors of my logo. My logo is phoenix so maybe incorporating flames similar to that design. I would like the back a solid color maybe red with an opaque version of the logo and website. As a marketing company I am always open to creative liberty!

Target Market(s)

Doctors and business professionals.

Industry/Entity Type

Marketing

Contact Information for Business Card

Valcorne Health Care Marketing
Marla Tenwick- CEO
#(512)638-2974
email-marla@valcorne.com
website- valcorne.com

Font styles to use
Sans Serif

Colors
ec1f27
f37122
ffc214
fbed22
fbf289
f04a50

Requirements
Must have
• The logo and required information
Nice to have
• icons by the information
Should not have
• child like font

```html
<!DOCTYPE html>
<html lang="en">
<head>
<meta charset="utf-8">
<title>Valcorne Health Care Marketing — Business Card</title>
<link rel="stylesheet" href="https://fonts.googleapis.com/css2?family=Raleway:wght@300;400&family=Arimo:wght@400;700&display=swap">
<style>
  :root {
    --backdrop: #262626;
    --card-red: #b2373a;
    --card-white: #ffffff;
    --brand-red: #c1272d;
    --brand-orange: #f3a11e;
    --flame-orange: #f37122;
    --ink-grey: #555555;
    --rule-grey: #9a9a9a;
    --logo-red: #d9534f;
  }
  * { box-sizing: border-box; margin: 0; padding: 0; }
  html, body { width: 1200px; height: 950px; overflow: hidden; }
  body {
    background: var(--backdrop);
    display: flex;
    flex-direction: column;
    align-items: center;
    justify-content: center;
    gap: 50px;
    font-family: "Arimo", Arial, sans-serif;
  }
  .card {
    width: 700px;
    height: 400px;
    position: relative;
    box-shadow: 0 14px 30px rgba(0,0,0,.45);
  }

  /* Back side */
  .card-back {
    background: var(--card-red);
    display: flex;
    flex-direction: column;
    align-items: center;
    justify-content: center;
    gap: 48px;
    color: #fff;
  }
  .brand {
    display: flex;
    align-items: center;
    gap: 22px;
  }
  .brand-dot {
    width: 78px; height: 78px; border-radius: 50%;
    flex: none;
  }
  .brand-name {
    font-family: "Raleway", Arial, sans-serif;
    font-weight: 300;
    line-height: 1.1;
    text-transform: uppercase;
  }
  .brand-name .word { display: block; font-size: 50px; letter-spacing: 1px; }
  .brand-name .tag {
    display: block; font-size: 17px; letter-spacing: 1px;
    border-top: 1px solid currentColor; padding-top: 5px; margin-top: 4px;
  }
  .card-back .brand-dot { background: #fff; opacity: .9; }
  .card-back .brand-name { color: #fff; }
  .web-address {
    font-size: 18px;
    letter-spacing: 6px;
  }

  /* Front side */
  .card-front { background: var(--card-white); }
  .card-front .brand {
    position: absolute;
    top: 52px; right: 62px;
  }
  .card-front .brand-dot { background: var(--flame-orange); width: 66px; height: 66px; }
  .card-front .brand-name { color: var(--logo-red); }
  .card-front .brand-name .word { font-size: 42px; }
  .card-front .brand-name .tag { font-size: 14px; }
  .divider {
    position: absolute;
    left: 48px; right: 48px;
    border: 0; border-top: 1px solid var(--rule-grey);
  }
  .divider-top { top: 196px; }
  .holder {
    position: absolute;
    left: 48px; top: 262px;
  }
  .holder-name {
    font-weight: 700; font-size: 26px; color: var(--brand-red);
  }
  .holder-role {
    font-size: 19px; color: var(--brand-orange); margin-top: 6px;
  }
  .divider-bottom { top: 340px; }
  .contact-row {
    position: absolute;
    left: 48px; top: 352px;
    display: flex; align-items: center; gap: 20px;
    list-style: none;
    font-size: 17px; color: var(--ink-grey);
  }
  .contact-row li { display: flex; align-items: center; gap: 7px; }
  .contact-icon { width: 18px; height: 18px; fill: var(--brand-red); flex: none; }
</style>
</head>
<body>

<section class="card card-back" aria-label="Card back">
  <div class="brand">
    <span class="brand-dot"></span>
    <p class="brand-name"><span class="word">Valcorne</span><span class="tag">Health Care Marketing</span></p>
  </div>
  <p class="web-address">www.valcorne.com</p>
</section>

<section class="card card-front" aria-label="Card front">
  <div class="brand">
    <span class="brand-dot"></span>
    <p class="brand-name"><span class="word">Valcorne</span><span class="tag">Health Care Marketing</span></p>
  </div>
  <hr class="divider divider-top">
  <div class="holder">
    <p class="holder-name">Marla Tenwick</p>
    <p class="holder-role">CEO</p>
  </div>
  <hr class="divider divider-bottom">
  <ul class="contact-row">
    <li>
      <svg class="contact-icon" viewBox="0 0 24 24" aria-hidden="true"><path d="M6.6 10.8c1.4 2.8 3.8 5.1 6.6 6.6l2.2-2.2c.3-.3.7-.4 1-.2 1.1.4 2.3.6 3.6.6.6 0 1 .4 1 1V20c0 .6-.4 1-1 1C10.6 21 3 13.4 3 4c0-.6.4-1 1-1h3.5c.6 0 1 .4 1 1 0 1.3.2 2.5.6 3.6.1.3 0 .7-.2 1z"/></svg>
      (512)638-2974
    </li>
    <li>
      <svg class="contact-icon" viewBox="0 0 24 24" aria-hidden="true"><path d="M2 5h20v14H2z M2 5l10 7 10-7" /><path d="M2 5l10 7 10-7v2l-10 7L2 7z" fill="#fff"/></svg>
      marla@valcorne.com
    </li>
    <li>
      <svg class="contact-icon" viewBox="0 0 24 24" aria-hidden="true"><circle cx="12" cy="12" r="10"/><path d="M2 12h20M12 2c3 3 3 17 0 20M12 2c-3 3-3 17 0 20" stroke="#fff" stroke-width="1.5" fill="none"/></svg>
      www.valcorne.com
    </li>
  </ul>
</section>

</body>
</html>
```